Duct Manufacturing Company new to the industry needs business card and stationary design

we are sheet metal duct manufacturers looking for a business card design to fit my new business logo.
nothing to crazy that will date, but want it to stand out from the crowed.
I'm sure you guys will work it out.

Contact Information for Business Card

Glen Marsh
Director

Address
17 Dorwell St
Carrowfield NSW 2741

0438 760 514

Sales@flowbend.com.au

Font styles to use
Other font styles liked:
• BankGothic md bt

Requirements
Nice to have
• Like the idea of corner rounded to match logo
• like to keep colours flowing
• font I like sharp square not rounded

```html
<!DOCTYPE html>
<html lang="en">
<head>
<meta charset="utf-8">
<title>Flowbend Industries – Business Card</title>
<link href="https://fonts.googleapis.com/css2?family=Michroma&display=swap" rel="stylesheet">
<style>
  :root {
    --page: #e9e7e3;
    --card-white: #f7f7f7;
    --blue-deep: #0a5fae;
    --blue-bright: #1a86d6;
    --green: #8cc63f;
    --ink-white: #ffffff;
    --logo-blue: #1b8fd2;
  }
  * { margin: 0; padding: 0; box-sizing: border-box; }
  html, body { width: 1200px; height: 780px; overflow: hidden; }
  body {
    background: var(--page);
    font-family: "Michroma", sans-serif;
    display: flex;
    align-items: center;
    justify-content: center;
  }
  .business-card {
    position: relative;
    width: 900px;
    height: 540px;
    border-radius: 34px;
    overflow: hidden;
    background: var(--card-white);
    box-shadow: 0 18px 40px rgba(0,0,0,0.18);
  }
  .card-background { position: absolute; inset: 0; width: 100%; height: 100%; }
  .contact-panel {
    position: absolute;
    left: 50px;
    top: 80px;
    color: var(--ink-white);
    text-transform: uppercase;
    white-space: nowrap;
  }
  .contact-name { font-size: 30px; letter-spacing: 3px; line-height: 1.1; }
  .contact-role { font-size: 13px; letter-spacing: 3px; margin-top: 8px; }
  .contact-details { margin-top: 70px; font-size: 15px; letter-spacing: 2px; line-height: 2; }
  .contact-line { display: flex; align-items: center; gap: 12px; }
  .contact-icon { width: 22px; height: 22px; flex: none; }
  .brand-lockup {
    position: absolute;
    left: 505px;
    top: 230px;
    display: flex;
    align-items: center;
    gap: 18px;
    color: var(--logo-blue);
    text-transform: uppercase;
    white-space: nowrap;
  }
  .brand-mark { width: 56px; height: 56px; border-radius: 50%; background: var(--logo-blue); flex: none; }
  .brand-name { font-size: 26px; letter-spacing: 3px; line-height: 1.35; }
</style>
</head>
<body>
  <div class="business-card">
    <svg class="card-background" viewBox="0 0 900 540" aria-hidden="true">
      <defs>
        <linearGradient id="blueSide" x1="0" y1="0" x2="1" y2="1">
          <stop offset="0" stop-color="#1a86d6"/>
          <stop offset="1" stop-color="#0a5fae"/>
        </linearGradient>
      </defs>
      <path d="M0 0 H400 Q500 270 430 540 H0 Z" fill="url(#blueSide)"/>
      <path d="M400 0 Q500 270 430 540" fill="none" stroke="#8cc63f" stroke-width="5"/>
    </svg>

    <div class="contact-panel">
      <div class="contact-name">Glen Marsh</div>
      <div class="contact-role">Director</div>
      <div class="contact-details">
        <div class="contact-line">17 Dorwell St</div>
        <div class="contact-line">Carrowfield NSW 2741</div>
        <div class="contact-line">
          <svg class="contact-icon" viewBox="0 0 24 24" aria-hidden="true">
            <rect x="1" y="1" width="22" height="22" rx="4" fill="#fff"/>
            <path d="M8 6 L10 6 L11 9 L9.5 10.5 Q11 13.5 13.5 14.5 L15 13 L18 14 L18 16 Q15 19 10 15 Q6 11 8 6 Z" fill="#0a5fae"/>
          </svg>
          0438 760 514
        </div>
        <div class="contact-line">
          <svg class="contact-icon" viewBox="0 0 24 24" aria-hidden="true">
            <rect x="1" y="1" width="22" height="22" rx="4" fill="#fff"/>
            <rect x="5" y="7" width="14" height="10" fill="none" stroke="#0a5fae" stroke-width="1.6"/>
            <path d="M5 7 L12 13 L19 7" fill="none" stroke="#0a5fae" stroke-width="1.6"/>
          </svg>
          Sales@flowbend.com.au
        </div>
      </div>
    </div>

    <div class="brand-lockup">
      <div class="brand-mark"></div>
      <div class="brand-name">Flowbend<br>Industries</div>
    </div>
  </div>
</body>
</html>
```